Local fast-growing company in the service sector

We are looking for a modern business card design, which should also appear on our letterheads

Target Market(s)

Private and industrial sectors

Contact Information for Business Card

Vorname Name
Kellberger Str. 18
73614 Lindhausen
Tel.: 07146-839214-0
Name@agentur-kvtl.de

Colors
9d9d9d
919191
aaaaaa

Requirements
Must have
• The logo (file) in silver

```html
<!DOCTYPE html>
<html lang="de">
<head>
<meta charset="utf-8">
<title>KVTL – Visitenkarte</title>
<link rel="stylesheet" href="https://fonts.googleapis.com/css2?family=Orbitron:wght@700&family=Roboto:wght@400&display=swap">
<style>
  :root {
    --backdrop: #2b2b2b;
    --card: #161616;
    --silver: #aaaaaa;
    --silver-mid: #9d9d9d;
    --silver-dark: #919191;
    --text-light: #e6e6e6;
  }
  * { margin: 0; padding: 0; box-sizing: border-box; }
  html, body {
    width: 800px;
    height: 1200px;
    overflow: hidden;
    background: var(--backdrop);
  }
  .sheet {
    width: 800px;
    height: 1200px;
    display: flex;
    flex-direction: column;
    justify-content: space-evenly;
    align-items: center;
  }
  .card {
    width: 620px;
    height: 400px;
    background: var(--card);
    position: relative;
  }
  .card-front {
    display: flex;
    align-items: center;
    justify-content: center;
  }
  .brand {
    display: flex;
    align-items: center;
    gap: 16px;
    font-family: "Orbitron", sans-serif;
    font-weight: 700;
    color: var(--silver);
    white-space: nowrap;
  }
  .brand-mark {
    background: var(--silver);
    flex: none;
  }
  .brand-large { font-size: 72px; letter-spacing: 4px; }
  .brand-large .brand-mark { width: 44px; height: 44px; }
  .brand-small { font-size: 38px; letter-spacing: 2px; gap: 12px; }
  .brand-small .brand-mark { width: 24px; height: 24px; }

  .card-back {
    display: flex;
    align-items: center;
    padding: 0 40px 0 48px;
  }
  .card-back .brand { width: 292px; flex: none; }
  .contact {
    color: var(--text-light);
    font-family: "Roboto", sans-serif;
  }
  .contact-name {
    font-family: "Orbitron", sans-serif;
    font-weight: 700;
    font-size: 20px;
    letter-spacing: 1.5px;
    white-space: nowrap;
    margin-bottom: 12px;
  }
  .contact-lines { list-style: none; font-size: 14px; line-height: 22px; color: var(--silver); white-space: nowrap; }
  .contact-lines li { display: flex; align-items: center; gap: 8px; }
  .contact-lines .indent { padding-left: 20px; }
  .icon { width: 12px; height: 12px; fill: var(--silver); flex: none; }
</style>
</head>
<body>
<main class="sheet">
  <section class="card card-front" aria-label="Vorderseite">
    <div class="brand brand-large"><span class="brand-mark"></span>KVTL</div>
  </section>

  <section class="card card-back" aria-label="Rückseite">
    <div class="brand brand-small"><span class="brand-mark"></span>KVTL</div>
    <div class="contact">
      <p class="contact-name">VORNAME NAME</p>
      <ul class="contact-lines">
        <li class="indent">Kellberger Str. 18</li>
        <li>
          <svg class="icon" viewBox="0 0 12 12" aria-hidden="true"><path d="M6 0a4 4 0 0 0-4 4c0 3 4 8 4 8s4-5 4-8a4 4 0 0 0-4-4zm0 5.6A1.6 1.6 0 1 1 6 2.4a1.6 1.6 0 0 1 0 3.2z"/></svg>
          73614 Lindhausen
        </li>
        <li>
          <svg class="icon" viewBox="0 0 12 12" aria-hidden="true"><path d="M2.4 0.5l2 2.4-1.2 1.5a7 7 0 0 0 4.4 4.4l1.5-1.2 2.4 2-1.3 1.9C5 11 1 7 0.5 1.8z"/></svg>
          07146-839214-0
        </li>
        <li>
          <svg class="icon" viewBox="0 0 12 12" aria-hidden="true"><path d="M0 2h12v1.2L6 7 0 3.2zM0 4.6l6 3.8 6-3.8V10H0z"/></svg>
          Name@agentur-kvtl.de
        </li>
      </ul>
    </div>
  </section>
</main>
</body>
</html>
```